Values and Organizational Purpose Signage

We recently solidified our company values, organizatioanal purpose and strategic vision. I'd like to develop some tasteful (not overly corporate) signage of these values to display in our office.

I've attached the hand-written values and purpose that my core team members then initialed acknowleding they align along with the signage at the front of our office to provide some perspective on our brand identity.

Industry/Entity Type

It Company

Font styles to use
Sans Serif

Requirements
Must have
• I'd like to see the values and org purpose depicted as one sign and as separate signs (i.e., values on one sign and org purpose on another). I need it to reflect our brand identity which I've uploaded

```html
<!DOCTYPE html>
<html lang="en">
<head>
<meta charset="utf-8">
<title>Brightmoor – Purpose and Values Signage</title>
<link rel="stylesheet" href="https://fonts.googleapis.com/css2?family=Jost:wght@400;500;700&display=swap">
<style>
  :root {
    --ink: #00363a;
    --lime: #9bd234;
    --panel: #ffffff;
    --wall-light: #6cb02a;
    --wall-mid: #4f8f06;
    --wall-dark: #233f04;
  }
  * { box-sizing: border-box; margin: 0; padding: 0; }
  html, body { width: 902px; height: 1200px; overflow: hidden; }
  body {
    position: relative;
    font-family: "Jost", sans-serif;
    color: var(--ink);
    background:
      radial-gradient(ellipse 90% 70% at 65% 20%, var(--wall-light) 0%, var(--wall-mid) 45%, var(--wall-dark) 100%);
  }
  .sign {
    position: absolute;
    left: 90px;
    width: 706px;
    background: var(--panel);
    box-shadow: 0 14px 30px rgba(0, 0, 0, 0.35);
  }
  .sign--purpose { top: 84px; height: 419px; }
  .sign--values { top: 603px; height: 482px; }

  .screw {
    position: absolute;
    width: 9px; height: 9px;
    border-radius: 50%;
    background: var(--ink);
  }
  .screw--tl { left: 8px; top: 13px; }
  .screw--tr { right: 8px; top: 13px; }
  .screw--bl { left: 8px; bottom: 8px; }
  .screw--br { right: 8px; bottom: 8px; }

  .brand {
    position: absolute;
    left: 0; right: 0; top: 80px;
    display: flex; justify-content: center; align-items: center; gap: 16px;
    font-size: 52px; font-weight: 700; line-height: 1;
    color: var(--ink);
  }
  .brand__dot { width: 24px; height: 24px; border-radius: 50%; background: var(--lime); }

  .sign__title {
    position: absolute;
    left: 54px;
    font-weight: 700;
    line-height: 1;
    white-space: nowrap;
  }
  .sign--purpose .sign__title { top: 232px; font-size: 41px; }
  .sign--values .sign__title { top: 50px; font-size: 51px; }

  .rule {
    position: absolute;
    height: 4px;
    background: var(--lime);
  }
  .sign--purpose .rule { left: 54px; width: 593px; top: 289px; }

  .purpose-text {
    position: absolute;
    left: 54px; top: 308px;
    font-size: 31px; font-weight: 500; line-height: 41px;
  }

  .value-label {
    position: absolute;
    left: 57px;
    font-size: 26px; font-weight: 700; line-height: 29px;
    letter-spacing: 0.3px;
  }
  .value-text {
    position: absolute;
    left: 306px;
    font-size: 19.5px; font-weight: 500; line-height: 24px;
  }
  .sign--values .rule { left: 57px; width: 593px; }
</style>
</head>
<body>
  <section class="sign sign--purpose">
    <span class="screw screw--tl"></span><span class="screw screw--tr"></span>
    <span class="screw screw--bl"></span><span class="screw screw--br"></span>
    <div class="brand"><span class="brand__dot"></span>Brightmoor</div>
    <h1 class="sign__title">ORGANIZATIONAL PURPOSE</h1>
    <div class="rule"></div>
    <p class="purpose-text">We deliver simple and digestible<br>solutions to complex matters</p>
  </section>

  <section class="sign sign--values">
    <span class="screw screw--tl"></span><span class="screw screw--tr"></span>
    <span class="screw screw--bl"></span><span class="screw screw--br"></span>
    <h2 class="sign__title">CORE VALUES DEFINED</h2>

    <h3 class="value-label" style="top:149px">RESPECT</h3>
    <p class="value-text" style="top:133px">We are transparent and receptive to the<br>thoughts, opinion and feelings of others</p>
    <div class="rule" style="top:189px"></div>

    <h3 class="value-label" style="top:228px">INTEGRITY</h3>
    <p class="value-text" style="top:226px">We uphold our promises</p>
    <div class="rule" style="top:272px"></div>

    <h3 class="value-label" style="top:311px">EXCELLENCE</h3>
    <p class="value-text" style="top:294px">We continuously strive to be the best in<br>all endeavors</p>
    <div class="rule" style="top:354px"></div>

    <h3 class="value-label" style="top:380px">OPEN<br>MINDEDNESS</h3>
    <p class="value-text" style="top:382px">We encourage creative and innovative<br>expressions</p>
  </section>
</body>
</html>
```